BrindleStaffing Business Card Design

We are a staffing company finding positions for dedicated nurses and physicians.

Target Market(s)

Business Professionals

Industry/Entity Type

Staffing

Contact Information for Business Card

Gordon Pratley
Chairman
417 39th Avenue South
SAINT PETERSBURG FL 33712
813-555-4172 Mobile
813-555-8036 Fax
gpratley@brindlestaffing.com
www.brindlestaffing.com

Font styles to use
Sans Serif

Colors
fbee3e
f04a50
f37122

Requirements
Must have
• Logo Attached, see colors below. We'd like to see Yellow, Orange and Red.

```html
<!DOCTYPE html>
<html lang="en">
<head>
<meta charset="utf-8">
<title>BrindleStaffing Business Card</title>
<link rel="stylesheet" href="https://fonts.googleapis.com/css2?family=Nunito:wght@800;900&family=Questrial&family=Poppins:wght@600&display=swap">
<style>
  :root {
    --backdrop: #2a2a2a;
    --paper: #ffffff;
    --brand-red: #f04a50;
    --brand-orange: #f37122;
    --brand-yellow: #fbee3e;
    --ink-grey: #5e5e5e;
    --rule-grey: #cfcfcf;
    --white: #ffffff;
  }
  * { box-sizing: border-box; margin: 0; padding: 0; }
  html, body {
    width: 1125px; height: 1200px; overflow: hidden;
    background: var(--backdrop);
  }
  .canvas { position: relative; width: 1125px; height: 1200px; }
  .card {
    position: absolute; left: 162px; width: 800px; height: 457px; overflow: hidden;
  }
  .card-front { top: 98px; background: var(--paper); }
  .card-back { top: 630px; background: var(--brand-red); }

  .wordmark {
    position: absolute; left: 40px; top: 190px;
    font-family: "Poppins", sans-serif; font-weight: 600;
    font-size: 42px; letter-spacing: -1.5px; color: var(--brand-red);
    display: flex; align-items: center; gap: 10px; line-height: 1;
  }
  .wordmark-dot { width: 14px; height: 14px; border-radius: 50%; background: var(--brand-yellow); }

  .divider { position: absolute; left: 418px; top: 100px; width: 1px; height: 216px; background: var(--rule-grey); }

  .contact { position: absolute; left: 452px; top: 102px; }
  .contact-name {
    font-family: "Nunito", sans-serif; font-weight: 900; font-size: 31px;
    color: var(--brand-red); line-height: 1;
  }
  .contact-title {
    font-family: "Nunito", sans-serif; font-weight: 800; font-size: 20px;
    color: var(--brand-orange); margin: 3px 0 0 2px; line-height: 1;
  }
  .contact-address {
    font-family: "Questrial", sans-serif; font-size: 18px; color: var(--ink-grey);
    line-height: 24px; margin-top: 18px;
  }
  .contact-lines { list-style: none; margin-top: 14px; }
  .contact-lines li {
    display: flex; align-items: center; gap: 12px; height: 26px;
    font-family: "Questrial", sans-serif; font-size: 18px; color: var(--ink-grey);
  }
  .contact-lines svg { width: 20px; height: 20px; fill: var(--brand-red); flex: none; }

  .web-band {
    position: absolute; left: 0; top: 386px; width: 693px; height: 33px;
    background: var(--brand-orange); color: var(--white);
    font-family: "Questrial", sans-serif; font-size: 19px; letter-spacing: 11px;
    line-height: 33px; padding-left: 130px; white-space: nowrap;
  }
  .cross-mark { position: absolute; left: 697px; top: 375px; width: 56px; height: 54px; }

  .back-brand { position: absolute; right: 46px; bottom: 40px; }
  .back-wordmark {
    font-family: "Poppins", sans-serif; font-weight: 600; font-size: 37px;
    letter-spacing: -1px; color: var(--white); line-height: 1.1;
  }
  .back-web {
    font-family: "Questrial", sans-serif; font-size: 18px; letter-spacing: 2.8px;
    color: var(--white); margin-top: 2px; white-space: nowrap;
  }
</style>
</head>
<body>
<main class="canvas">
  <section class="card card-front">
    <div class="wordmark"><span class="wordmark-dot"></span>BrindleStaffing</div>
    <div class="divider"></div>
    <div class="contact">
      <h1 class="contact-name">Gordon Pratley</h1>
      <p class="contact-title">Chairman</p>
      <p class="contact-address">417 39th Avenue South<br>SAINT PETERSBURG FL 33712</p>
      <ul class="contact-lines">
        <li>
          <svg viewBox="0 0 20 20" aria-hidden="true"><path d="M6 1h8a2 2 0 0 1 2 2v14a2 2 0 0 1-2 2H6a2 2 0 0 1-2-2V3a2 2 0 0 1 2-2zm0 3v11h8V4zm4 12.2a.9.9 0 1 0 0 1.8.9.9 0 0 0 0-1.8z"/></svg>
          813-555-4172
        </li>
        <li>
          <svg viewBox="0 0 20 20" aria-hidden="true"><path d="M5 2h8l2 2v3H5zM2 8h16a1 1 0 0 1 1 1v6a1 1 0 0 1-1 1h-2v2H4v-2H2a1 1 0 0 1-1-1V9a1 1 0 0 1 1-1zm4 5v3h8v-3z"/></svg>
          813-555-8036
        </li>
        <li>
          <svg viewBox="0 0 20 20" aria-hidden="true"><path d="M2 5h16v10H2zm1.5 1.2L10 11l6.5-4.8V6h-13z" fill-rule="evenodd"/></svg>
          gpratley@brindlestaffing.com
        </li>
      </ul>
    </div>
    <div class="web-band">www.brindlestaffing.com</div>
    <svg class="cross-mark" viewBox="0 0 56 54" aria-hidden="true">
      <path d="M18 0h20v17h18v20H38v17H18V37H0V17h18z" fill="var(--brand-red)"/>
    </svg>
  </section>

  <section class="card card-back">
    <div class="back-brand">
      <div class="back-wordmark">BrindleStaffing</div>
      <div class="back-web">www.brindlestaffing.com</div>
    </div>
  </section>
</main>
</body>
</html>
```